Business card for medical clinic

I need an upmarket, modern medical/health business card for my clinic

Contact Information for Business Card

name, address, email, qr code

```html
<!DOCTYPE html>
<html lang="en">
<head>
<meta charset="utf-8">
<title>Meridian Care Clinic – Business Card</title>
<link href="https://fonts.googleapis.com/css2?family=Poppins:wght@300;400;600&display=swap" rel="stylesheet">
<style>
  :root {
    --stage: #222224;
    --card-dark: #1e1f23;
    --card-dark-band: #17181b;
    --brand-blue: #1ea3dc;
    --deep-navy: #1b2a4a;
    --text-light: #f2f4f7;
    --text-muted: #d9dde3;
  }
  * { box-sizing: border-box; margin: 0; padding: 0; }
  html, body {
    width: 1200px; height: 780px; overflow: hidden;
    background: var(--stage);
    font-family: "Poppins", Arial, sans-serif;
  }
  .canvas {
    position: relative; width: 1200px; height: 780px;
    display: flex; align-items: center; justify-content: center; gap: 50px;
  }
  .card {
    position: relative; width: 525px; height: 300px;
    border-radius: 4px; overflow: hidden;
    box-shadow: 0 18px 40px rgba(0,0,0,.55);
  }

  /* Back side: contact details */
  .card-back {
    background: var(--card-dark);
    color: var(--text-light);
    text-align: center;
  }
  .card-back .shade-band {
    position: absolute; left: 0; right: 0; top: 70px; height: 150px;
    background: linear-gradient(180deg, rgba(0,0,0,0) 0%, var(--card-dark-band) 40%, var(--card-dark-band) 60%, rgba(0,0,0,0) 100%);
  }
  .card-back .content { position: relative; padding-top: 28px; }
  .brand-small {
    display: inline-flex; align-items: center; gap: 8px;
    font-weight: 400; font-size: 13px; letter-spacing: 2px;
    color: var(--brand-blue); text-transform: uppercase;
  }
  .brand-dot {
    width: 14px; height: 14px; border-radius: 50%;
    border: 2px solid var(--brand-blue);
  }
  .person-name {
    margin-top: 18px; font-size: 30px; line-height: 1.1;
    color: var(--brand-blue);
  }
  .person-name .first { font-weight: 600; }
  .person-name .last { font-weight: 300; }
  .person-title { font-size: 11.5px; font-weight: 400; color: var(--text-light); margin-top: 2px; }
  .icon-row { display: flex; justify-content: center; gap: 6px; margin-top: 12px; }
  .icon {
    width: 17px; height: 17px; border-radius: 50%;
    background: var(--brand-blue); display: flex; align-items: center; justify-content: center;
  }
  .icon svg { width: 10px; height: 10px; }
  .contact-list { list-style: none; margin-top: 6px; font-size: 12px; line-height: 1.55; color: var(--text-muted); }
  .address-block { position: absolute; left: 0; right: 0; bottom: 16px; }
  .address-block .icon { margin: 0 auto 4px; }
  .address { font-size: 12.5px; color: var(--brand-blue); }

  /* Front side: brand */
  .card-front {
    background:
      radial-gradient(ellipse at 20% 95%, #22a9e2 0%, rgba(34,169,226,0) 60%),
      linear-gradient(205deg, var(--deep-navy) 0%, #1d5d8f 38%, #1c8fcb 65%, #1fa2dc 100%);
    display: flex; align-items: center; justify-content: center;
  }
  .brand-large {
    display: flex; align-items: center; gap: 16px;
    color: #ffffff; font-weight: 400; font-size: 26px; letter-spacing: 3px;
    text-transform: uppercase;
  }
  .brand-large .brand-dot { width: 34px; height: 34px; border: 3px solid #ffffff; }
</style>
</head>
<body>
<main class="canvas">
  <section class="card card-back" aria-label="Business card back">
    <div class="shade-band"></div>
    <div class="content">
      <div class="brand-small"><span class="brand-dot"></span>Meridian Care Clinic</div>
      <h1 class="person-name"><span class="first">Lena</span> <span class="last">Marrow</span></h1>
      <p class="person-title">Founder &amp; CEO</p>
      <div class="icon-row">
        <span class="icon"><svg viewBox="0 0 10 10"><path d="M2 1.2 L3.6 1 L4.2 3 L3.2 3.7 Q4 5.7 6.3 6.8 L7 5.8 L9 6.4 L8.8 8 Q5 8.6 2.2 5 Q1 3 2 1.2Z" fill="#fff"/></svg></span>
        <span class="icon"><svg viewBox="0 0 10 10"><rect x="1" y="2.3" width="8" height="5.4" rx=".6" fill="none" stroke="#fff" stroke-width="1"/><path d="M1.3 2.7 L5 5.4 L8.7 2.7" fill="none" stroke="#fff" stroke-width="1"/></svg></span>
        <span class="icon"><svg viewBox="0 0 10 10"><circle cx="5" cy="5" r="3.8" fill="none" stroke="#fff" stroke-width="1"/><ellipse cx="5" cy="5" rx="1.7" ry="3.8" fill="none" stroke="#fff" stroke-width=".8"/><path d="M1.2 5 H8.8" stroke="#fff" stroke-width=".8"/></svg></span>
      </div>
      <ul class="contact-list">
        <li>(555) 214-0386</li>
        <li>hello@meridiancare.com</li>
        <li>www.meridiancare.com</li>
      </ul>
    </div>
    <div class="address-block">
      <span class="icon"><svg viewBox="0 0 10 10"><path d="M5 9.2 Q2 5.6 2 3.9 A3 3 0 0 1 8 3.9 Q8 5.6 5 9.2Z" fill="#fff"/><circle cx="5" cy="3.9" r="1.1" fill="#1ea3dc"/></svg></span>
      <p class="address">418 Linden Ave. Suite 300 Riverton, CA 90417</p>
    </div>
  </section>

  <section class="card card-front" aria-label="Business card front">
    <div class="brand-large"><span class="brand-dot"></span>Meridian Care Clinic</div>
  </section>
</main>
</body>
</html>
```